Coastline Premier Retreats Business Card Design

Design a business card for Coastline Premier Retreats. Look at the website for colors and reference. Card should have logo, name, title, office number, mobile number, email, URL and a tagline like, "Luxury Hotel & Resort Email Marketing" (This might change).

https://www.coastlinepremierretreats.example

The rest I will leave up to your imagination.

Contact Information for Business Card

Logo, name, title, office number, mobile number, email, URL and a tagline like, "Luxury Hotel & Resort Email Marketing" (This might change).

```html
<!DOCTYPE html>
<html lang="en">
<head>
<meta charset="utf-8">
<title>Coastline Premier Retreats – Business Card</title>
<link rel="stylesheet" href="https://fonts.googleapis.com/css2?family=Michroma&family=Open+Sans:wght@400;600&display=swap">
<style>
  :root {
    --backdrop: #3b3b3b;
    --card-white: #ffffff;
    --card-black: #1b1b1b;
    --accent: #f26b1d;
    --ink: #141414;
    --muted: #6b6b6b;
    --light: #ffffff;
  }
  * { box-sizing: border-box; margin: 0; padding: 0; }
  html, body {
    width: 1200px; height: 801px; overflow: hidden;
    background: var(--backdrop);
  }
  .canvas {
    position: relative; width: 1200px; height: 801px;
    display: flex; align-items: center; justify-content: center; gap: 40px;
  }
  .card {
    position: relative; width: 520px; height: 298px;
    border-bottom: 3px solid var(--accent);
    border-radius: 2px;
  }
  .card--front { background: var(--card-white); }
  .card--back { background: var(--card-black); border: 1px solid var(--accent); border-top: none; border-left: none; }

  .brand-name {
    font-family: "Michroma", sans-serif;
    font-weight: 400;
    text-transform: uppercase;
    letter-spacing: 1px;
    line-height: 1.25;
    display: flex; align-items: center; gap: 12px;
  }
  .brand-name__square {
    width: 14px; height: 14px; background: var(--accent); flex: none;
  }
  .card--front .brand-name {
    position: absolute; left: 48px; top: 46px;
    font-size: 21px; color: var(--ink);
  }
  .card--back .brand-name {
    position: absolute; left: 0; right: 0; top: 86px;
    justify-content: center;
    font-size: 24px; color: var(--light);
  }

  .identity {
    position: absolute; left: 48px; top: 178px;
    font-family: "Open Sans", sans-serif;
  }
  .identity__name {
    font-weight: 600; font-size: 19px; letter-spacing: 0.5px;
    color: var(--accent); text-transform: uppercase;
  }
  .identity__title { font-size: 13px; color: var(--muted); margin-top: 2px; }

  .divider {
    position: absolute; left: 262px; top: 172px;
    width: 1px; height: 70px; background: var(--accent);
  }

  .contacts {
    position: absolute; left: 282px; top: 176px;
    list-style: none;
    font-family: "Open Sans", sans-serif; font-size: 11.5px; color: var(--muted);
  }
  .contacts li { display: flex; align-items: center; gap: 7px; height: 21px; white-space: nowrap; }
  .contacts svg { width: 11px; height: 11px; flex: none; fill: var(--accent); }

  .tagline {
    position: absolute; left: 0; right: 0; bottom: 56px;
    text-align: center;
    font-family: "Michroma", sans-serif; font-size: 11px;
    letter-spacing: 2.5px; color: var(--light); text-transform: uppercase;
  }
</style>
</head>
<body>
<main class="canvas">
  <section class="card card--front" aria-label="Business card front">
    <div class="brand-name"><span class="brand-name__square"></span><span>Coastline<br>Premier Retreats</span></div>
    <div class="identity">
      <p class="identity__name">Dorian Kessler</p>
      <p class="identity__title">President / CEO</p>
    </div>
    <div class="divider"></div>
    <ul class="contacts">
      <li><svg viewBox="0 0 24 24" aria-hidden="true"><path d="M6.6 10.8a15.1 15.1 0 0 0 6.6 6.6l2.2-2.2a1 1 0 0 1 1-.25 11.4 11.4 0 0 0 3.6.6 1 1 0 0 1 1 1V20a1 1 0 0 1-1 1A17 17 0 0 1 3 4a1 1 0 0 1 1-1h3.5a1 1 0 0 1 1 1c0 1.25.2 2.45.6 3.6a1 1 0 0 1-.25 1z"/></svg>555.214.7300</li>
      <li><svg viewBox="0 0 24 24" aria-hidden="true"><path d="M2 5h20v14H2z M2 5l10 8 10-8" /></svg>info@coastlinepremierretreats.example</li>
      <li><svg viewBox="0 0 24 24" aria-hidden="true"><circle cx="12" cy="12" r="10"/></svg>www.coastlinepremierretreats.example</li>
    </ul>
  </section>

  <section class="card card--back" aria-label="Business card back">
    <div class="brand-name"><span class="brand-name__square"></span><span>Coastline<br>Premier Retreats</span></div>
    <p class="tagline">Luxury Hotel &amp; Resort Email Marketing</p>
  </section>
</main>
</body>
</html>
```